Label design for an exciting new Vodka brand

We need a label design for a dynamic new Vodka brand called 'Pale lantern drift Vodka'. It is a crisp and versatile liquid with a clean and smooth finish. It should appeal to 21-39 year olds, with a slight female skew. Colours, fonts and styles should be modern and relatively neutral - take inspiration from the brand pictures attached.

Target Market(s)

21-39 year olds, both male and female, but with a slight female skew

```html
<!DOCTYPE html>
<html lang="en">
<head>
<meta charset="utf-8">
<title>Pale lantern drift Vodka – Label Set</title>
<link href="https://fonts.googleapis.com/css2?family=Montserrat:wght@200;300;400&display=swap" rel="stylesheet">
<style>
  :root {
    --page: #ffffff;
    --ink: #ffffff;
    --rose-ground: #f1b4b4;
    --iris-ground: #92a8f2;
    --label-w: 480px;
    --label-h: 640px;
  }
  * { margin: 0; padding: 0; box-sizing: border-box; }
  html, body {
    width: 1200px;
    height: 1200px;
    overflow: hidden;
    background: var(--page);
  }
  .canvas {
    position: relative;
    width: 1200px;
    height: 1200px;
    display: flex;
    justify-content: center;
    align-items: center;
    gap: 60px;
  }
  .label {
    position: relative;
    width: var(--label-w);
    height: var(--label-h);
    overflow: hidden;
    color: var(--ink);
    font-family: "Montserrat", sans-serif;
  }
  .label--rose { background: var(--rose-ground); }
  .label--iris { background: var(--iris-ground); }

  .label__line {
    position: absolute;
    left: 0;
    width: 100%;
    text-align: center;
    line-height: 1;
    white-space: nowrap;
    font-weight: 300;
  }
  .label__word-one {
    top: 54px;
    font-size: 125px;
    font-weight: 200;
  }
  .label__word-two {
    top: 200px;
    font-size: 60px;
  }
  .label__word-three {
    top: 270px;
    font-size: 58px;
    letter-spacing: 0.45em;
    padding-left: 0.45em;
  }
  .label__rule {
    position: absolute;
    top: 349px;
    left: 172px;
    width: 136px;
    height: 2px;
    background: var(--ink);
  }
  .label__category {
    top: 405px;
    font-size: 80px;
    letter-spacing: 0.4em;
    padding-left: 0.4em;
  }
</style>
</head>
<body>
  <main class="canvas">
    <article class="label label--rose" aria-label="Pale lantern drift Vodka label, rose edition">
      <h1 class="label__line label__word-one">PALE</h1>
      <p class="label__line label__word-two">LANTERN</p>
      <p class="label__line label__word-three">DRIFT</p>
      <div class="label__rule"></div>
      <p class="label__line label__category">VODKA</p>
    </article>

    <article class="label label--iris" aria-label="Pale lantern drift Vodka label, iris edition">
      <h2 class="label__line label__word-one">PALE</h2>
      <p class="label__line label__word-two">LANTERN</p>
      <p class="label__line label__word-three">DRIFT</p>
      <div class="label__rule"></div>
      <p class="label__line label__category">VODKA</p>
    </article>
  </main>
</body>
</html>
```